BOLD & MINIMALIST DESIGN NEEDED

We want a very bold but minimalistic business card design that is impactful and utilizes both sides of the business card. Our current logo is included for your use.

We want bold fonts and good use of negative space. We don't want the logo to overpower the design.

Target Market(s)

Professionals who are building new commercial buildings.

Industry/Entity Type

Construction

Contact Information for Business Card

Name, Title, email, office phone, cell phone, website

Font styles to use
Serif
Sans Serif

Requirements
Must have
• Bold design!

```html
<!DOCTYPE html>
<html lang="en">
<head>
<meta charset="utf-8">
<title>Ridgecrest Business Card</title>
<link href="https://fonts.googleapis.com/css2?family=Arimo:wght@400;700&display=swap" rel="stylesheet">
<style>
  :root {
    --page: #e4e4e4;
    --card-white: #ffffff;
    --ink: #111111;
    --text-grey: #555555;
    --lime: #8cc63f;
    --lime-light: #b5dc76;
    --lime-pale: #d2ecaa;
    --black: #000000;
  }
  * { margin: 0; padding: 0; box-sizing: border-box; }
  html, body {
    width: 1200px; height: 1200px; overflow: hidden;
    background: var(--page);
    font-family: "Arimo", Arial, sans-serif;
  }
  .card {
    position: absolute;
    left: 255px;
    width: 690px;
    height: 393px;
    overflow: hidden;
  }
  .card-front { top: 159px; background: var(--card-white); }
  .card-back {
    top: 653px;
    background: radial-gradient(ellipse at 50% 45%, var(--lime-light) 0%, var(--lime) 70%);
  }
  .brand {
    position: absolute;
    display: flex; align-items: center; gap: 10px;
    font-weight: 700;
    letter-spacing: 0.5px;
  }
  .brand-mark { display: block; background: var(--lime); }
  .card-front .brand {
    left: 118px; top: 176px;
    font-size: 30px; color: var(--ink);
  }
  .card-front .brand-mark { width: 22px; height: 22px; }
  .contact-block { position: absolute; left: 390px; top: 118px; }
  .person-name {
    font-size: 26px; font-weight: 700; color: var(--ink);
    letter-spacing: 0.5px; line-height: 1;
  }
  .person-title {
    font-size: 15px; color: var(--lime); margin-top: 8px;
  }
  .contact-list { list-style: none; margin-top: 18px; }
  .contact-list li {
    display: flex; align-items: center; gap: 10px;
    font-size: 16px; color: var(--text-grey);
    height: 21px;
  }
  .contact-list svg { width: 14px; height: 14px; flex: none; }
  .swoosh { position: absolute; left: 0; bottom: 0; width: 690px; height: 393px; }
  .card-back .brand {
    left: 0; right: 0; top: 0; bottom: 0;
    justify-content: center;
    font-size: 58px; color: var(--lime-pale);
  }
  .card-back .brand-mark { width: 38px; height: 38px; background: var(--lime-pale); }
</style>
</head>
<body>
  <section class="card card-front">
    <div class="brand"><span class="brand-mark"></span>RIDGECREST</div>

    <div class="contact-block">
      <h1 class="person-name">DANIEL HARPER</h1>
      <p class="person-title">President</p>
      <ul class="contact-list">
        <li>
          <svg viewBox="0 0 14 14"><path d="M3 1 L5.5 1 L6.5 4 L5 5.3 Q6.5 8.3 9 9.3 L10.3 8 L13 9 L13 11.5 Q12 13 10 12.8 Q3 11 1.2 4 Q1 2 3 1Z" fill="#111"/></svg>
          555-214-7390
        </li>
        <li>
          <svg viewBox="0 0 14 14"><rect x="3.5" y="0.8" width="7" height="12.4" rx="1" fill="none" stroke="#111" stroke-width="1.6"/><rect x="6" y="10.6" width="2" height="1.2" fill="#111"/></svg>
          555-382-6615
        </li>
        <li>
          <svg viewBox="0 0 14 14"><rect x="1" y="3" width="12" height="8.5" fill="#111"/><path d="M1.5 3.5 L7 8 L12.5 3.5" fill="none" stroke="#fff" stroke-width="1.2"/></svg>
          hello@ridgecrestbuild.com
        </li>
        <li>
          <svg viewBox="0 0 14 14"><circle cx="7" cy="7" r="6" fill="#111"/><path d="M4 4 Q6 5 5 7 Q7 8 6 11 M9 3 Q8 5 10 6" fill="none" stroke="#fff" stroke-width="1.1"/></svg>
          www.ridgecrestbuild.com
        </li>
      </ul>
    </div>

    <svg class="swoosh" viewBox="0 0 690 393" aria-hidden="true">
      <path d="M0 382 Q345 312 690 382 L690 393 L0 393Z" fill="var(--lime)"/>
      <path d="M0 382 Q345 334 690 382" fill="none" stroke="#fff" stroke-width="3"/>
      <path d="M0 380 Q345 352 690 380 L690 393 L0 393Z" fill="var(--black)"/>
    </svg>
  </section>

  <section class="card card-back">
    <div class="brand"><span class="brand-mark"></span>RIDGECREST</div>
  </section>
</body>
</html>
```